Zelvo Stationary

Design the stationary of Zelvo Promotions Group.

Zelvo is a BTL company, BTL meaning "below the line". In other words Zelvo is a Promotional Marketing company (the company that design the brands promotional activities).

The design should transmit creativity, agility, boldness.

I need:
* Bis Card
* Letter head
* Envelopes, both vertical and horizontal (for legal size), and letter envelope
* Folders
* PPT template (Title page and regular page)
* CD slip (CD envelope)
* ID card (employee card)

And what ever else you want to throw in.
Updates

Guys,

Something I missed from the brief.   The predominat color should be RED.

Also, have fun and play with the exclamation mark (!) of the logo. 

Hi guys, more comments:

Remember that Zelvo is a "creativity" agency, not in the advertising side but on the promotional side, and that should reflect on the stationary.

 I want a bold design.  Bold and yet crisp.

 

Guys, i just uploaded the Logo in AI format.

I Also uploaded the actual Zelvo Bis Card, wich I like.  So I will like to see some designs with that bis card approach.

Guys, I am so sorry, but I notice in your last post that I upladed a wrong design ("13154_promotions_group_zelvo_brief225630.ai").  The problem was that I asked the designer the file in AI format and he send me thw wrong file, and since I dont have Illustrator I could not verify it.

The differences are minor, I just already ask him the correct one (similar to the EPS file).

Sorry                                   

Just post the correct AI file : "Zelvo Logo.ai"

Reason: I'm expecting more designs to choose from and also I wont be available tomorrow to decide.

Reason: Sorry guys, but we are not there yet!

Target Market(s)

Marketing directors, Marketing Managers

Industry/Entity Type

Legal

Requirements
Must have
• Must work with the logo attached.
The predominat color should be RED.
Play and have fun with the exclamation mark (!).
Should not have
• * No old fonts

Should not be:
* boring
* Informal
* rigid

```html
<!DOCTYPE html>
<html lang="en">
<head>
<meta charset="utf-8">
<title>Zelvo Promotions Group — Business Card</title>
<link href="https://fonts.googleapis.com/css2?family=Arimo:wght@400;700&display=swap" rel="stylesheet">
<style>
  :root {
    --brand-red: #b3121c;
    --charcoal: #2a2a2c;
    --ink: #1a1a1a;
    --text-grey: #3a3a3a;
    --paper: #ffffff;
    --page: #ffffff;
  }
  * { margin: 0; padding: 0; box-sizing: border-box; }
  html, body {
    width: 1200px; height: 900px; overflow: hidden;
    background: var(--page);
    font-family: "Arimo", Arial, sans-serif;
  }
  .sheet { position: relative; width: 1200px; height: 900px; }
  .sheet-title {
    position: absolute; top: 68px; left: 0; width: 1180px;
    text-align: center; font-size: 27px; font-weight: 700; color: var(--ink);
  }
  .card {
    position: absolute; width: 516px; height: 296px;
    box-shadow: 6px 7px 10px rgba(0,0,0,0.35);
    background: var(--paper);
  }
  .card svg { display: block; width: 100%; height: 100%; }
  .card--front-red { left: 62px; top: 176px; }
  .card--white-rays { left: 632px; top: 176px; }
  .card--band-red { left: 62px; top: 500px; }
  .card--band-rays { left: 632px; top: 500px; }

  .fill-red { fill: var(--brand-red); }
  .fill-white { fill: var(--paper); }
  .fill-charcoal { fill: var(--charcoal); }
  .stroke-rule { stroke: var(--text-grey); stroke-width: 1; }

  .t-name { font-family: "Arimo", Arial, sans-serif; font-weight: 700; font-size: 19px; }
  .t-contact { font-family: "Arimo", Arial, sans-serif; font-size: 12px; }
  .t-address { font-family: "Arimo", Arial, sans-serif; font-size: 10.5px; }
  .t-web { font-family: "Arimo", Arial, sans-serif; font-weight: 700; font-size: 12px; }
  .t-wordmark { font-family: "Arimo", Arial, sans-serif; font-weight: 700; font-size: 50px; letter-spacing: -1px; }
  .on-red { fill: var(--paper); }
  .on-white { fill: var(--text-grey); }
  .ink { fill: var(--ink); }
</style>
</head>
<body>
<main class="sheet">
  <h1 class="sheet-title">business card</h1>

  <!-- Card 1: red with white diagonal -->
  <div class="card card--front-red">
    <svg viewBox="0 0 516 296">
      <rect class="fill-red" width="516" height="296"/>
      <polygon class="fill-white" points="0,198 516,104 516,296 0,296"/>
      <text class="t-name on-red" x="478" y="42" text-anchor="end">MARCO DELVAR</text>
      <polygon class="fill-white" points="486,28 506,28 486,44"/>
      <text class="t-contact on-red" x="500" y="66" text-anchor="end">marco.delvar@zelvo.com.do</text>
      <text class="t-contact on-red" x="500" y="84" text-anchor="end">809-555-0172</text>
      <text class="t-address on-red" x="22" y="112">27 Calle Norte, Los Prados,</text>
      <text class="t-address on-red" x="22" y="125">Santo Domingo, Dominican Republic</text>
      <text class="t-address on-red" x="22" y="138">Phone: +809.555.0140, Fax: +809.555.0141</text>
      <text class="t-address on-red" x="22" y="151">E-mail: info@zelvo.com.do</text>
      <text class="t-web on-red" x="22" y="176">www.zelvo.com.do</text>
      <rect class="fill-red" x="328" y="216" width="14" height="14"/>
      <text class="t-wordmark ink" x="480" y="268" text-anchor="end">zelvo</text>
    </svg>
  </div>

  <!-- Card 2: white with red rays -->
  <div class="card card--white-rays">
    <svg viewBox="0 0 516 296">
      <rect class="fill-white" width="516" height="296"/>
      <text class="t-name ink" transform="translate(40,236) rotate(-90)"><tspan class="fill-red">▸</tspan> MARCO DELVAR</text>
      <text class="t-contact on-white" transform="translate(60,236) rotate(-90)">marco.delvar@zelvo.com.do</text>
      <text class="t-contact on-white" transform="translate(76,236) rotate(-90)">809-555-0172</text>
      <line class="stroke-rule" x1="100" y1="28" x2="100" y2="236"/>
      <text class="t-wordmark ink" x="150" y="112">zelvo</text>
      <rect class="fill-red" x="290" y="78" width="14" height="14"/>
      <polygon class="fill-red" points="388,52 452,0 516,0 410,66"/>
      <polygon class="fill-red" points="420,80 516,44 516,84 424,100"/>
      <polygon class="fill-red" points="420,118 516,124 516,164 414,138"/>
      <polygon class="fill-red" points="400,152 500,206 476,228 390,168"/>
      <text class="t-address on-white" x="152" y="170">27 Calle Norte, Los Prados,</text>
      <text class="t-address on-white" x="152" y="183">Santo Domingo, Dominican Republic</text>
      <text class="t-address on-white" x="152" y="196">Phone: +809.555.0140, Fax: +809.555.0141</text>
      <text class="t-address on-white" x="152" y="209">E-mail: info@zelvo.com.do</text>
      <text class="t-web ink" x="152" y="234">www.zelvo.com.do</text>
    </svg>
  </div>

  <!-- Card 3: charcoal band, red with white diagonal -->
  <div class="card card--band-red">
    <svg viewBox="0 0 516 296">
      <rect class="fill-red" width="516" height="296"/>
      <polygon class="fill-white" points="80,214 516,112 516,296 80,296"/>
      <rect class="fill-charcoal" width="80" height="296"/>
      <text class="t-name on-red" transform="translate(34,240) rotate(-90)"><tspan class="fill-red">▸</tspan> MARCO DELVAR</text>
      <text class="t-contact on-red" transform="translate(54,240) rotate(-90)">marco.delvar@zelvo.com.do</text>
      <text class="t-contact on-red" transform="translate(70,240) rotate(-90)">809-555-0172</text>
      <text class="t-address on-red" x="116" y="40">27 Calle Norte, Los Prados,</text>
      <text class="t-address on-red" x="116" y="53">Santo Domingo, Dominican Republic</text>
      <text class="t-address on-red" x="116" y="66">Phone: +809.555.0140, Fax: +809.555.0141</text>
      <text class="t-address on-red" x="116" y="79">E-mail: info@zelvo.com.do</text>
      <text class="t-web on-red" x="116" y="104">www.zelvo.com.do</text>
      <rect class="fill-red" x="328" y="218" width="14" height="14"/>
      <text class="t-wordmark ink" x="480" y="270" text-anchor="end">zelvo</text>
    </svg>
  </div>

  <!-- Card 4: charcoal band, red with white rays -->
  <div class="card card--band-rays">
    <svg viewBox="0 0 516 296">
      <rect class="fill-red" width="516" height="296"/>
      <rect class="fill-charcoal" width="78" height="296"/>
      <text class="t-name on-red" transform="translate(34,240) rotate(-90)"><tspan class="fill-red">▸</tspan> MARCO DELVAR</text>
      <text class="t-contact on-red" transform="translate(54,240) rotate(-90)">marco.delvar@zelvo.com.do</text>
      <text class="t-contact on-red" transform="translate(70,240) rotate(-90)">809-555-0172</text>
      <text class="t-wordmark ink" x="118" y="100">zelvo</text>
      <rect class="fill-white" x="258" y="66" width="14" height="14"/>
      <polygon class="fill-white" points="392,48 456,0 516,0 412,64"/>
      <polygon class="fill-white" points="422,78 516,44 516,84 426,98"/>
      <polygon class="fill-white" points="422,118 516,124 516,164 416,138"/>
      <polygon class="fill-white" points="402,152 500,206 476,228 392,168"/>
      <text class="t-address on-red" x="120" y="164">27 Calle Norte, Los Prados,</text>
      <text class="t-address on-red" x="120" y="177">Santo Domingo, Dominican Republic</text>
      <text class="t-address on-red" x="120" y="190">Phone: +809.555.0140, Fax: +809.555.0141</text>
      <text class="t-address on-red" x="120" y="203">E-mail: info@zelvo.com.do</text>
      <text class="t-web on-red" x="120" y="228">www.zelvo.com.do</text>
    </svg>
  </div>
</main>
</body>
</html>
```